Two Wine Labels, One Red One White

We are looking to create a brand image for our wines. There are two requirements by law that we need, however beyond that, the creativity comes from the designer. Required are:
On The Red Label, Alcohol 14.1White Label Alcohol 12.5, The Size, 750ML
SO One label for the red wine with alcohol at 14.1 in a 750 ML Bottle, and one Label for white with alcohol at 12.5 in a 750 ML bottle.

Hi All:
I have some more clarity to assist in the design work.
The Brand Name of the wine is Valquine for both the red and the white
The name should appear as Valquine with the Brackets around phonetical as seen here
[val-keen] Both the word and the phonetical spelling should appear.
and can be seen on lexiquarry.com The Brand Name text can be black
Label should be very light grey, I am trying to capture a Stone grey or texture from stone, although, NOT Marble.
The Red Label, The word "Red" should be in red
The White Label, The word "White" should be in White, all the original remaining elements remain as originally posted.

I look forward to hearing from you for any additional questions.
Updates

Just added a logo Not really seeing what we are trying to achieve, maybe using the logo in the design may assist

Target Market(s)

Wine Aficionados

Requirements
Must have
• Details described in Project Description above, these are required by law. The Name of the Brand will be posted shortly. For the moment if you take the project, just place red on one label and white on the other.
Nice to have
• These two wines are from California (USA), so the Sierra Nevada Mountains could be an inspiration, to outline of California or coast line, a vineyard (of course), a vine...We are in silicon valley, so there is a map of silicon valley with the Bay and ocean, something from a map could work, or let your creativity flow and not use any of these concepts.
Should not have
• I do not not care for decorative fonts, however all else is open

```html
<!DOCTYPE html>
<html lang="en">
<head>
<meta charset="utf-8">
<title>Valquine Wine Labels</title>
<link rel="stylesheet" href="https://fonts.googleapis.com/css2?family=Questrial&family=Open+Sans:wght@300;400&display=swap">
<style>
  :root {
    --backdrop: #130004;
    --label-paper: #ffffff;
    --ink: #111111;
    --red-wine: #ec1c24;
    --white-wine: #d8e021;
    --band-text: #ffffff;
  }
  * { box-sizing: border-box; margin: 0; padding: 0; }
  html, body {
    width: 1200px; height: 900px; overflow: hidden;
    background: var(--backdrop);
  }
  .canvas { position: relative; width: 1200px; height: 900px; }
  .label {
    position: absolute; top: 141px;
    width: 443px; height: 617px;
    background: var(--label-paper);
    text-align: center;
  }
  .label--red { left: 134px; --accent: var(--red-wine); }
  .label--white { left: 623px; --accent: var(--white-wine); }

  .landscape {
    position: absolute; left: 0; top: 75px;
    width: 100%; height: 204px;
  }
  .label--red .landscape {
    background: linear-gradient(170deg, #3ab8e6 0%, #c8522e 55%, #d27a38 100%);
  }
  .label--white .landscape {
    background: linear-gradient(170deg, #5a8fc0 0%, #9c6e48 55%, #b8884c 100%);
  }

  .brand-name {
    position: absolute; left: 0; right: 0; top: 303px;
    font-family: "Questrial", sans-serif;
    font-size: 66px; font-weight: 400; color: var(--ink);
    line-height: 1;
  }
  .phonetic {
    position: absolute; left: 0; right: 0; top: 380px;
    font-family: "Questrial", sans-serif;
    font-size: 27px; color: var(--accent); line-height: 1;
  }
  .variety-band {
    position: absolute; left: 0; top: 420px;
    width: 100%; height: 66px;
    background: var(--accent);
    font-family: "Open Sans", sans-serif; font-weight: 400;
    font-size: 72px; line-height: 66px; color: var(--band-text);
    overflow: hidden; white-space: nowrap;
  }
  .label--red .variety-band { letter-spacing: 44px; padding-left: 50px; }
  .label--white .variety-band { letter-spacing: 36px; padding-left: 36px; }

  .legal {
    position: absolute; left: 0; right: 0; top: 535px;
    font-family: "Open Sans", sans-serif;
    font-size: 20px; color: var(--ink); line-height: 34px;
  }
</style>
</head>
<body>
<main class="canvas">
  <section class="label label--red">
    <div class="landscape" role="img" aria-label="Painterly landscape of red and orange mountains above a blue lake under a bright sky"></div>
    <h1 class="brand-name">Valquine</h1>
    <p class="phonetic">[val-keen]</p>
    <p class="variety-band">RED</p>
    <p class="legal">Alcohol 14.1<br>750мл.</p>
  </section>
  <section class="label label--white">
    <div class="landscape" role="img" aria-label="Painterly landscape of muted brown and golden mountains above a blue lake under a soft sky"></div>
    <h1 class="brand-name">Valquine</h1>
    <p class="phonetic">[val-keen]</p>
    <p class="variety-band">WHITE</p>
    <p class="legal">Alcohol 12.5<br>750мл.</p>
  </section>
</main>
</body>
</html>
```